Business Card Design Project - del varosi group

dear Sirs

we need business card design for our group ( DEL Varosi Group ) , i have got the Logo design of our group from pixel harbor in previous , so all need details relating to our group i think available with you, as well as the the chosen logo design

we hope to provide us with business card logo that to be appropaite and satisfactory to us .

thanks

note : logo design of our group is attached .
Updates

Reason: please extend the deadline of my project for additional 15 days because i didn't received appropriate design for our gruop yet . kindly beaware that i have received 77 design till now , supossed to send me 200-250 design at least . thanks

Target Market(s)

contents

name : Kerem EL Nadiri

position : Operation Manager

Industry/Entity Type

Business

Requirements
Must have

• person name

group logo
Nice to have
• logo color matching with back background

```html
<!DOCTYPE html>
<html lang="en">
<head>
<meta charset="utf-8">
<title>DEL Varosi Group – Business Card</title>
<link rel="stylesheet" href="https://fonts.googleapis.com/css2?family=Open+Sans:wght@400;600;700&display=swap">
<style>
  :root {
    --bg: #e9e7e4;
    --card-white: #ffffff;
    --brand-blue: #0d5aa7;
    --brand-blue-dark: #0a4a8c;
    --brand-blue-light: #1b74c9;
    --rule: #0d5aa7;
    --text-light: #ffffff;
    --shadow: rgba(0, 0, 0, 0.25);
  }
  * { box-sizing: border-box; margin: 0; padding: 0; }
  html, body {
    width: 1200px; height: 758px; overflow: hidden;
    background: var(--bg);
    font-family: "Open Sans", Arial, sans-serif;
  }
  .stage { position: relative; width: 1200px; height: 758px; }

  .card {
    position: absolute; top: 219px;
    width: 500px; height: 300px;
    border-radius: 24px; overflow: hidden;
    box-shadow: 0 10px 28px var(--shadow);
  }
  .card--front { left: 70px; background: var(--card-white); }
  .card--back {
    left: 630px;
    background: linear-gradient(135deg, var(--brand-blue-dark), var(--brand-blue-light));
    color: var(--text-light);
  }

  /* front */
  .front-top { height: 138px; display: flex; align-items: center; justify-content: center; }
  .brand-name {
    display: flex; align-items: center; gap: 12px;
    color: var(--brand-blue); font-weight: 700; font-size: 34px; letter-spacing: 1px;
  }
  .brand-name .mark { width: 22px; height: 22px; background: currentColor; }
  .front-bottom {
    position: absolute; left: 0; right: 0; bottom: 0; height: 162px;
    background: var(--brand-blue);
    border-top: 3px solid var(--card-white);
    box-shadow: 0 -2px 0 var(--rule);
  }
  .name-bar {
    position: absolute; left: 112px; right: 32px; top: -12px; height: 28px;
    background: var(--brand-blue-light);
    display: flex; align-items: center; padding-left: 22px;
    color: var(--text-light);
  }
  .person-name { font-weight: 700; font-size: 16px; }
  .person-role { font-size: 12px; margin-left: 6px; }
  .details {
    position: absolute; left: 0; right: 0; top: 34px;
    display: flex; color: var(--text-light); font-size: 12.5px; line-height: 1.45;
  }
  .address {
    width: 250px; text-align: right; padding-right: 14px;
    display: flex; flex-direction: column; justify-content: center;
  }
  .divider { width: 1px; background: rgba(255,255,255,0.6); margin: 4px 0; }
  .contacts { list-style: none; padding-left: 12px; }
  .contacts li { display: flex; align-items: center; gap: 6px; }
  .contacts svg { width: 10px; height: 10px; fill: var(--text-light); flex: none; }

  /* back */
  .back-brand {
    position: absolute; left: 0; right: 0; top: 96px;
    display: flex; justify-content: center; align-items: center; gap: 12px;
    font-weight: 700; font-size: 34px; letter-spacing: 1px; color: var(--text-light);
  }
  .back-brand .mark { width: 22px; height: 22px; background: currentColor; }
  .back-web {
    position: absolute; left: 0; right: 0; top: 200px; text-align: center;
    font-size: 19px; letter-spacing: 1.5px;
  }
</style>
</head>
<body>
<main class="stage">
  <section class="card card--front" aria-label="Business card front">
    <div class="front-top">
      <div class="brand-name"><span class="mark"></span>DEL VAROSI GROUP</div>
    </div>
    <div class="front-bottom">
      <div class="name-bar">
        <span class="person-name">Kerem EL Nadiri,</span>
        <span class="person-role">Operation Manager</span>
      </div>
      <div class="details">
        <div class="address">
          <span>Street name, City</span>
          <span>State, zip code</span>
        </div>
        <div class="divider"></div>
        <ul class="contacts">
          <li><svg viewBox="0 0 10 10"><rect x="2.5" y="0.5" width="5" height="9" rx="1"/></svg>+2347014829305</li>
          <li><svg viewBox="0 0 10 10"><path d="M2 1l2 0 1 2.5-1.2 1a5 5 0 0 0 2.7 2.7l1-1.2L10 7v2a1 1 0 0 1-1 1A8 8 0 0 1 1 2a1 1 0 0 1 1-1z"/></svg>+2347014829305</li>
          <li><svg viewBox="0 0 10 10"><circle cx="5" cy="3" r="2.4"/><path d="M0.8 10a4.2 4.2 0 0 1 8.4 0z"/></svg>+2347014829305</li>
          <li><svg viewBox="0 0 10 10"><rect x="0.5" y="2" width="9" height="6.5" rx="1"/></svg>name@marlowinns.com</li>
          <li><svg viewBox="0 0 10 10"><circle cx="5" cy="5" r="4.5"/></svg>www.website.com</li>
        </ul>
      </div>
    </div>
  </section>

  <section class="card card--back" aria-label="Business card back">
    <div class="back-brand"><span class="mark"></span>DEL VAROSI GROUP</div>
    <p class="back-web">www.website.com</p>
  </section>
</main>
</body>
</html>
```